Web Design Project

Crest Tide needs a new web page design.

This final product MUST be a layered .psd format for our CSS coder to do properly.

What we need is a 3 column template similar to the attached sample. We NEED to have 3 defined sections "Learn" "Shop" and "Dive." This is very important.

Our store font is Ethnocentric, so any design which incorporates this somehow would be great. Our logo is attached in a .jpeg and .psd format. Feel free to manipulate the logo background into a design that works.

Preferred colors are blue (not light blue,) grey, black and yellow. The center section of the template must remain white.

Crest Tide is a website for technical and rebreather equipment, and training. PLEASE do NOT show images of recreational scuba divers. This is not our market and designs featuring recreational 'touristy' divers will be eliminated.

Attached are logos, and images for use as a background image.

Target Market(s)

Males 25-60

Industry/Entity Type

Store

Requirements
Must have
• - 3 defined sections "Learn" "Shop" "Dive"
- White center area
- Final format must be delivered in a layered .psd file for our CSS coder to cut
Nice to have
• -Ethnocentric fonts
-3d borders
-Textures
- Blue, great black, yellow colors.
- Simple, uncluttered design
Should not have
• Images or logos of recreational or 'tourist' scuba divers. This is a technical and rebreather diving business.

Light blue colors

```html
<!DOCTYPE html>
<html lang="en">
<head>
<meta charset="utf-8">
<title>Crest Tide Store</title>
<link href="https://fonts.googleapis.com/css2?family=Open+Sans:wght@400;600;700&display=swap" rel="stylesheet">
<style>
:root{
  --navy:#112440;
  --panel:#ffffff;
  --blue:#1d6fc4;
  --blue-dark:#0f4f9c;
  --blue-light:#3a8ee0;
  --link:#2a7fd0;
  --orange:#e2581c;
  --rust:#b3460f;
  --ink:#2b2b2b;
  --body:#555555;
  --rule:#c9c9c9;
}
*{box-sizing:border-box;margin:0;padding:0}
html,body{width:1200px;height:964px;overflow:hidden}
body{background:var(--navy);font-family:"Open Sans",Arial,sans-serif;color:var(--ink);position:relative}
.abs{position:absolute}
.brand{left:162px;top:30px;display:flex;align-items:center;gap:12px;color:#fff;font-size:34px;font-weight:700;letter-spacing:.5px}
.brand .dot{width:26px;height:26px;border-radius:50%;background:#fff}
.topnav{left:506px;top:28px;width:556px;height:35px;border-radius:6px;background:linear-gradient(#ffffff,#e3e3e3);box-shadow:0 1px 3px rgba(0,0,0,.4);display:flex;font-size:13px}
.topnav a{color:#333;text-decoration:none;display:flex;align-items:center;justify-content:center;border-right:1px solid #c4c4c4;height:100%}
.topnav a:last-child{border-right:none;gap:8px}
.panel{left:136px;top:79px;width:926px;height:799px;background:var(--panel);border-radius:4px}
.search{left:393px;top:94px;width:298px;height:35px;border-radius:8px;border:1px solid #d3d3d3;box-shadow:0 2px 3px rgba(0,0,0,.15);font-size:13px;color:#333;padding:8px 12px}
.search svg{position:absolute;right:12px;top:8px}
.quick{top:100px;font-size:17.5px;color:#222;display:flex;align-items:center;gap:6px}
.quick::before{content:"";width:7px;height:7px;border-top:2px solid var(--orange);border-right:2px solid var(--orange);transform:rotate(45deg);margin-right:4px}
.call{left:393px;top:148px;font-size:17.5px;color:var(--rust)}
.call span{color:var(--link);font-size:23px;margin-left:4px}
.ship{right:178px;top:144px;font-size:13px;color:#222}
.head{top:197px;height:34px;border-radius:6px;background:linear-gradient(var(--blue-light),var(--blue-dark));color:#fff;font-size:16px;padding:6px 14px;box-shadow:0 2px 3px rgba(0,0,0,.25)}
.head::after{content:"";position:absolute;right:10px;bottom:-8px;border-left:8px solid transparent;border-right:8px solid transparent;border-top:9px solid var(--blue-dark)}
.learn-item{left:155px;width:180px}
.learn-item h3{font-weight:400;font-size:14px;color:#222;white-space:nowrap}
.photo{background:linear-gradient(160deg,#b9b4aa,#6f6a63);width:178px}
.learn-item p{font-size:12.5px;line-height:18px;color:var(--body);text-align:justify;width:178px;margin-top:9px}
.watch{font-size:13px;color:var(--orange);margin-top:9px}
.tile{width:143px;height:142px;border:1px solid var(--rule);box-shadow:0 1px 3px rgba(0,0,0,.2);background:#fff;padding:2px}
.tile div{width:100%;height:100%;background:linear-gradient(150deg,#e4e4e4,#8a8a8a)}
.label{width:143px;text-align:center;font-size:13px;color:var(--orange)}
.dive{left:855px;width:190px}
.dive h3{font-weight:400;font-size:14px;color:#222}
.dive .date{font-size:12px;color:var(--link);margin-top:1px}
.dive p{font-size:12px;line-height:16.4px;color:var(--body);margin-top:9px;text-align:justify}
.dive .more{font-size:12px;color:var(--link);margin-top:10px}
.foot{right:142px;top:904px;font-size:12.5px;color:#d8dde6}
</style>
</head>
<body>
<div class="abs brand"><span class="dot"></span>Crest Tide</div>

<nav class="abs topnav">
  <a style="width:101px">Home</a>
  <a style="width:97px">About Us</a>
  <a style="width:103px">Send Mail</a>
  <a style="width:115px">Privacy Policy</a>
  <a style="width:140px"><svg width="20" height="18" viewBox="0 0 20 18"><path d="M1 2h3l3 10h9l2-7H6" fill="none" stroke="#e2581c" stroke-width="2"/><circle cx="8" cy="15.5" r="1.6" fill="#e2581c"/><circle cx="15" cy="15.5" r="1.6" fill="#e2581c"/></svg>View Cart</a>
</nav>

<div class="abs panel"></div>

<div class="abs search">Search<svg width="18" height="18" viewBox="0 0 18 18"><circle cx="7" cy="7" r="5" fill="none" stroke="#2a7fd0" stroke-width="2.2"/><path d="M11 11l5 5" stroke="#2a7fd0" stroke-width="2.6" stroke-linecap="round"/></svg></div>

<div class="abs quick" style="left:736px">Best Sellers</div>
<div class="abs quick" style="left:862px">New Arrivals</div>
<div class="abs quick" style="left:1001px">Sale</div>

<div class="abs call">Questions? Call Us!<span>555.300.0142</span></div>
<div class="abs ship">Shipping International?&nbsp; Click for Details</div>

<div class="abs head" style="left:150px;width:186px">Learn</div>
<div class="abs head" style="left:371px;width:454px">Shop</div>
<div class="abs head" style="left:855px;width:190px">Dive</div>

<section class="learn">
  <div class="abs learn-item" style="top:257px">
    <h3>Sanitol disinfectant</h3>
    <div class="photo" style="height:113px;margin-top:8px" role="img" aria-label="Staff member presenting a disinfectant bottle in the workshop"></div>
    <p>Crest Tide's Nora Vale Speaks about our new disinfec-</p>
    <div class="watch">Watch Video</div>
  </div>

  <div class="abs learn-item" style="top:507px">
    <h3>Ready to pick your rebreather?</h3>
    <div class="photo" style="height:117px;margin-top:11px" role="img" aria-label="Instructor seated behind a rebreather unit"></div>
    <p>Wade Harlan is certified to dive or instruct and sell over 8 different types of units. Read our articles to get unbaised reveiws, tips and tricks from a group that doesn't have an agenda!</p>
    <div class="watch">Watch Video</div>
  </div>
</section>

<section class="shop">
  <div class="abs tile" style="left:371px;top:267px"><div role="img" aria-label="Backplate and wing harness"></div></div>
  <div class="abs tile" style="left:526px;top:267px"><div role="img" aria-label="Dive computers and controllers"></div></div>
  <div class="abs tile" style="left:680px;top:267px"><div role="img" aria-label="Drysuit accessories and argon bottle"></div></div>
  <div class="abs label" style="left:371px;top:421px">Backplates / Wings</div>
  <div class="abs label" style="left:526px;top:421px">Electronics</div>
  <div class="abs label" style="left:680px;top:421px">Exposure Protection</div>

  <div class="abs tile" style="left:371px;top:465px"><div role="img" aria-label="Steel and aluminium cylinders"></div></div>
  <div class="abs tile" style="left:526px;top:465px"><div role="img" aria-label="O-rings, plates and clips"></div></div>
  <div class="abs tile" style="left:680px;top:465px"><div role="img" aria-label="Dive torches and canister light"></div></div>
  <div class="abs label" style="left:371px;top:617px">Tanks</div>
  <div class="abs label" style="left:526px;top:617px">Hardware</div>
  <div class="abs label" style="left:680px;top:617px">Lights</div>

  <div class="abs tile" style="left:371px;top:662px"><div role="img" aria-label="Scrubber absorbent and rebreather bag"></div></div>
  <div class="abs tile" style="left:526px;top:662px"><div role="img" aria-label="Regulator set with gauge"></div></div>
  <div class="abs tile" style="left:680px;top:662px"><div role="img" aria-label="Marker buoy, compass and reel"></div></div>
  <div class="abs label" style="left:371px;top:816px">Rebreathers</div>
  <div class="abs label" style="left:526px;top:816px">Regulators</div>
  <div class="abs label" style="left:680px;top:816px">Other Gear</div>
</section>

<section>
  <div class="abs dive" style="top:248px">
    <h3>Deepwater 2012!</h3>
    <div class="date">May 26 June2, 2012</div>
    <p>Join Wade, Marco and Lena along with over 60 other CCR divers for a great week of divingGrand Cayman's deep walls</p>
    <div class="more">Read More &gt;&gt;</div>
  </div>
  <div class="abs dive" style="top:405px">
    <h3>Truck Lagoon CCR Trip</h3>
    <div class="date">July 13, 2012</div>
    <p>Wade and Nora make another trip out to dive the deep wreks of Truck. Let Crest Tide make your trip easy by taking care</p>
    <div class="more">Read More &gt;&gt;</div>
  </div>
  <div class="abs dive" style="top:568px">
    <h3>Deepwater 2012!</h3>
    <div class="date">May 26 June2, 2012</div>
    <p>Join Wade, Marco and Lena along with over 60 other CCR divers for a great week of divingGrand Cayman's deep walls</p>
    <div class="more">Read More &gt;&gt;</div>
  </div>
</section>

<footer class="abs foot">Copyrights @ 2012 All Rights Reserved</footer>
</body>
</html>
```